Modern card design needed for building development company

We are looking for a sharp modern new look for our business cards.
We are a New Zealand based company called TKR Ventures NZ LTD that specialises in subdividing large sections, housing and commercial buildings.
We have attached a photo of the current logo and would like to see it improved somehow as it looks a bit dated.
We are open to any colours.

Target Market(s)

Investors, Property buyers

Industry/Entity Type

Investment

Contact Information for Business Card

TKR VENTURES NZ LTD
www.tkrventuresnz.co.nz

Damon Whitcombe
Phone +64 21 938 104
Email dpwhitcombe@korumail.co.nz

Font styles to use
Serif
Sans Serif

Colors
0792cd
33a6d7
85cae6
6b449b
886aae
f04a50
ec1f27
f37122
f68d4d

Requirements
Must have
• Please try and make the logo more modern or if you have a similar one we would like to see it.

```html
<!DOCTYPE html>
<html lang="en">
<head>
<meta charset="utf-8">
<title>TKR Ventures NZ LTD – Business Card</title>
<link href="https://fonts.googleapis.com/css2?family=Montserrat:wght@500;700&family=Work+Sans:wght@400&display=swap" rel="stylesheet">
<style>
  :root {
    --page-bg: #e4e4e4;
    --card-dark: #2a2a2a;
    --card-light: #ffffff;
    --brand-red: #9b1b30;
    --ink: #2b2b2b;
    --ink-soft: #444444;
    --white: #ffffff;
  }
  * { margin: 0; padding: 0; box-sizing: border-box; }
  html, body { width: 1200px; height: 900px; overflow: hidden; }
  body {
    background: var(--page-bg);
    position: relative;
    font-family: "Work Sans", Arial, sans-serif;
  }
  .card {
    position: absolute;
    left: 270px;
    width: 660px;
    height: 377px;
    border-radius: 22px;
    overflow: hidden;
    box-shadow: 0 8px 24px rgba(0,0,0,0.18);
  }
  .card-back { top: 44px; background: var(--card-dark); }
  .card-front { top: 472px; background: var(--card-light); }

  .back-wordmark {
    position: absolute;
    inset: 0;
    display: flex;
    align-items: center;
    justify-content: center;
    font-family: "Montserrat", Arial, sans-serif;
    font-weight: 500;
    font-size: 30px;
    letter-spacing: 5px;
    color: var(--white);
  }

  .front-brand {
    position: absolute;
    left: 48px;
    top: 118px;
    width: 220px;
    display: flex;
    flex-direction: column;
    align-items: center;
    gap: 14px;
  }
  .brand-square {
    width: 54px;
    height: 54px;
    background: var(--brand-red);
  }
  .brand-name {
    font-family: "Montserrat", Arial, sans-serif;
    font-weight: 700;
    font-size: 14px;
    letter-spacing: 2px;
    color: var(--brand-red);
    white-space: nowrap;
  }
  .divider {
    position: absolute;
    left: 300px;
    top: 70px;
    width: 2px;
    height: 165px;
    background: var(--ink);
  }
  .contact {
    position: absolute;
    left: 338px;
    top: 70px;
    color: var(--ink-soft);
  }
  .contact-name {
    font-family: "Montserrat", Arial, sans-serif;
    font-weight: 700;
    font-size: 24px;
    letter-spacing: 0.5px;
    color: var(--brand-red);
    line-height: 1;
  }
  .contact-role { font-size: 15px; margin-top: 4px; }
  .contact-address { font-size: 15.5px; line-height: 1.3; margin-top: 14px; }
  .contact-lines { list-style: none; margin-top: 10px; font-size: 15.5px; line-height: 1.45; }
  .contact-lines li { display: flex; align-items: center; gap: 10px; }
  .contact-lines svg { width: 13px; height: 13px; flex: none; }

  .front-wave { position: absolute; left: 0; bottom: 0; width: 660px; height: 150px; }
</style>
</head>
<body>
  <section class="card card-back" aria-label="Card back">
    <div class="back-wordmark">TKR VENTURES NZ LTD</div>
  </section>

  <section class="card card-front" aria-label="Card front">
    <div class="front-brand">
      <div class="brand-square"></div>
      <div class="brand-name">TKR VENTURES NZ LTD</div>
    </div>

    <div class="divider"></div>

    <div class="contact">
      <h1 class="contact-name">DAMON WHITCOMBE</h1>
      <p class="contact-role">Director</p>
      <p class="contact-address">PO BOX 48215 Devonport<br>Auckland New Zealand</p>
      <ul class="contact-lines">
        <li>
          <svg viewBox="0 0 16 16" aria-hidden="true"><path d="M4 1.5 L6.5 4.5 L5 6.5 Q6.5 9.5 9.5 11 L11.5 9.5 L14.5 12 L12.5 14.5 Q6 14 1.5 3.5 Z" fill="var(--brand-red)"/></svg>
          +64 21 938 104
        </li>
        <li>
          <svg viewBox="0 0 16 16" aria-hidden="true"><rect x="1.5" y="3.5" width="13" height="9" fill="none" stroke="var(--brand-red)" stroke-width="1.4"/><path d="M1.5 3.5 L8 9 L14.5 3.5" fill="none" stroke="var(--brand-red)" stroke-width="1.4"/></svg>
          dpwhitcombe@korumail.co.nz
        </li>
        <li>
          <svg viewBox="0 0 16 16" aria-hidden="true"><g fill="none" stroke="var(--brand-red)" stroke-width="1.2"><circle cx="8" cy="8" r="6.5"/><ellipse cx="8" cy="8" rx="3" ry="6.5"/><path d="M1.5 8 H14.5 M2.5 4.8 H13.5 M2.5 11.2 H13.5"/></g></svg>
          www.tkrventuresnz.co.nz
        </li>
      </ul>
    </div>

    <svg class="front-wave" viewBox="0 0 660 150" preserveAspectRatio="none" aria-hidden="true">
      <path d="M0 40 C 140 90, 300 70, 420 72 C 540 74, 610 110, 660 150 L 660 150 L 0 150 Z" fill="var(--card-dark)"/>
      <path d="M0 34 C 140 84, 300 62, 420 64 C 540 66, 610 102, 660 142" fill="none" stroke="var(--brand-red)" stroke-width="6"/>
    </svg>
  </section>
</body>
</html>
```